Birchwell Agency Condominium mail merge

We need a marketing proposal letter design to do a mail merge to potential e customers. We included our logo and an example of my miserable attempt to create a template. We are looking for a modern and attractive proposal template. Here is our website https://www.birchwellagency.example to be used for any additional information needed about us and our services.

Target Market(s)

New prospects

Industry/Entity Type

Insurance Agency

Requirements
Must have
• My project must have a modern professional look with merge fields similar to the file uploaded with this project.
Nice to have
• it would like have a condominium and a car icon graphic depicting there is additional discounts for both quotes bundled.
Should not have
• My project should not have any other logos or company name

```html
<!DOCTYPE html>
<html lang="en">
<head>
<meta charset="utf-8">
<title>Birchwell Agency Letterhead</title>
<link rel="stylesheet" href="https://fonts.googleapis.com/css2?family=Source+Sans+3:wght@400;600;700&family=Arimo:wght@700&display=swap">
<style>
  :root {
    --green: #3db54a;
    --orange: #f47b20;
    --ink: #2b2b2b;
    --heading: #444444;
    --backdrop: #e6e6e6;
    --paper: #ffffff;
  }
  * { margin: 0; padding: 0; box-sizing: border-box; }
  html, body { width: 1059px; height: 1200px; overflow: hidden; background: var(--backdrop); }
  .sheet {
    position: absolute; left: 121px; top: 24px;
    width: 816px; height: 1152px; background: var(--paper);
    font-family: "Source Sans 3", sans-serif; color: var(--ink);
  }
  .brand {
    position: absolute; left: 64px; top: 72px;
    display: flex; align-items: center; gap: 10px;
  }
  .brand-dot { width: 18px; height: 18px; border-radius: 50%; background: var(--orange); }
  .brand-name { font-size: 31px; font-weight: 700; color: var(--green); letter-spacing: 0.2px; }
  .contact { position: absolute; left: 621px; top: 39px; font-size: 12.5px; line-height: 16.5px; }
  .contact-name { color: var(--green); font-weight: 700; font-size: 13px; }
  .contact-role { color: var(--orange); }
  .contact-line { display: flex; align-items: center; gap: 6px; }
  .contact-line svg { width: 10px; height: 10px; fill: var(--green); }
  .contact-address { font-size: 11px; line-height: 16px; margin-top: 2px; }
  .salutation {
    position: absolute; left: 61px; top: 230px;
    font-family: "Arimo", sans-serif; font-weight: 700; font-size: 18px; color: var(--heading);
  }
  .body-copy { position: absolute; left: 62px; top: 278px; width: 692px; }
  .body-copy p {
    font-size: 16.6px; line-height: 21.4px; text-align: justify; margin-bottom: 21.4px;
  }
  .signature {
    position: absolute; left: 62px; top: 853px; width: 154px; height: 73px;
    background: linear-gradient(135deg, #f4f4f4, #e4e4e4);
  }
  .footer { position: absolute; left: 0; bottom: 0; width: 816px; height: 28px; }
  .footer-url {
    position: absolute; left: 578px; bottom: 7px;
    font-size: 11.5px; font-weight: 700; letter-spacing: 2px; color: #fff;
  }
</style>
</head>
<body>
<div class="sheet">
  <div class="brand">
    <span class="brand-dot"></span>
    <span class="brand-name">Birchwell Agency</span>
  </div>

  <div class="contact">
    <div class="contact-name">Nolan Birchwell</div>
    <div class="contact-role">Agency Principal</div>
    <div class="contact-line">
      <svg viewBox="0 0 10 10"><path d="M2 0.5l1.6 2.2-1 1c.6 1.4 1.5 2.3 2.8 2.8l1-1 2.2 1.6-1 1.8C4 8.6 1.4 6 0.3 1.5z"/></svg>
      <span>555-014-2278</span>
    </div>
    <div class="contact-line">
      <svg viewBox="0 0 10 10"><path d="M0 2h10v6H0z M0 2l5 3.5L10 2" fill="var(--green)" stroke="#fff" stroke-width="0.8"/></svg>
      <span>nolan@birchwellagency.example</span>
    </div>
    <div class="contact-address">742 Lakeview Parkway<br>Ste. 210 Maplewood, FL 32000</div>
  </div>

  <h1 class="salutation">Dear Mr. Carter,</h1>

  <div class="body-copy">
    <p>Lorem Ipsum is simply dummy text of the printing and typesetting industry. Lorem Ipsum has been the industry's standard dummy text ever since the 1500s, when an unknown printer took a galley of type and scrambled it to make a type specimen book. It has survived not only five centuries, but also the leap into electronic typesetting, remaining essentially unchanged.</p>
    <p>The standard chunk of Lorem Ipsum used since the 1500s is reproduced below for those interested. Sections 1.10.32 and 1.10.33 from "de Finibus Bonorum et Malorum" by Aulus Fenn are also reproduced in their exact original form, accompanied by English versions from the 1914 translation by H. Marlow</p>
    <p>Lorem Ipsum is simply dummy text of the printing and typesetting industry. Lorem Ipsum has been the industry's standard dummy text ever since the 1500s, when an unknown printer took a galley of type and scrambled it to make a type specimen book. It has survived not only five centuries, but also the leap into electronic typesetting, remaining essentially unchanged. It was popularised in the</p>
    <p>Lorem Ipsum is simply dummy text of the printing and typesetting industry. Lorem Ipsum has been the industry's standard dummy text ever since the 1500s, when an unknown printer took a galley of type and scrambled it to make a type specimen book. It has survived not only five centuries, but also the leap into electronic typesetting, remaining essentially unchanged. It was popularised in the</p>
    <p>Lorem Ipsum is simply dummy text of the printing and typesetting industry. Lorem Ipsum has been the industry's standard dummy text ever since the 1500s, when an unknown printer took a galley of type and scrambled it to make a type specimen book.</p>
  </div>

  <div class="signature" role="img" aria-label="Handwritten signature of the sender"></div>

  <svg class="footer" viewBox="0 0 816 28" preserveAspectRatio="none" aria-hidden="true">
    <rect x="0" y="6" width="562" height="6" fill="var(--orange)"/>
    <rect x="0" y="17" width="816" height="11" fill="var(--green)"/>
    <polygon points="577,0 816,0 816,28 557,28" fill="var(--green)"/>
  </svg>
  <div class="footer-url">www.birchwellagency.example</div>
</div>
</body>
</html>
```